Webdesign for a business that converts shops into apps. UPDATE BRIEF

We want a creative/professional design for our new business Vorbo.

Vorbo is a service that can deliver instant apps for quillora shops. So every shop owner can have its own app for selling to there customers.

We are open for your interpretation of the design. We think it could be intersting doing an onepage design for this. But thats not set in stones offcourse.

We need several section:
top section
some facts abt the service and maybe our company
price table
some customer review
functionalitys of the app (in a nice way shown)
Section showing screens of a demo shop.
footer with ccdetails, socialmedia, newsletter

I have been playing abit myself with a theme, but no development/designer experience. And we really need a very professional and custom look.

Ps. we are an ecommerce company so if we find any good designer here, we will have enough work for you.

Some competitors in this field;

http://shrt.example/k7Tq2Zw
http://shrt.example/p3Nx9Ld

Here is a design we like
http://brelunoweb.example/

Hoping for some great concepts!

Kind Regards and good luck!

Some screenshots which can be used for app demo;

UPDATE BRIEF

We would like to add a section for features of the app.
We would like to show a zelphone screen and all the most important features of the app and when clicking every feature the screen would change or the feature intened would be high lighted in some way.

The features and any content and info abt that can be used from
https://www.tovexa.example/features.html/

We need an how it works section aswell in the design, also that can be used content from here
https://www.tovexa.example/how-it-works/

Tovexa is our partner, so there work way and features are same as ours. We just want it in a different 'look and feel/design)

Reason: Getting very few good design at the moment. Same designers seem to be responding whith 5 designs at a time of low quality.

Target Market(s)

quillora webshop

Industry/Entity Type

Business

Number of Pages Required

1 page

Font styles to use
Sans Serif

Colors
0355a3
3176b5
85acd3
85cae6
33a6d7
0392cd
f59195
33b8a4

Requirements
Must have
• a creative and custom look, not a copied theme vibe.
Nice to have
• it would be nice if the entire design has a nice flow goinf through the site. The customers experience should be on point.
Should not have
• boring static experience

```html
<!DOCTYPE html>
<html lang="en">
<head>
<meta charset="utf-8">
<title>Vorbo – Instant apps for quillora shops</title>
<link href="https://fonts.googleapis.com/css2?family=Open+Sans:wght@300;400;600;700;800&display=swap" rel="stylesheet">
<style>
:root{
  --blue:#0355a3;
  --blue-mid:#1a63b0;
  --blue-light:#3176b5;
  --red:#ee4a50;
  --red-soft:#f59195;
  --ink:#2a2a2a;
  --text:#555;
  --muted:#a5a5a5;
  --panel:#f4f4f4;
  --footer:#efefef;
  --bottom:#1e2b38;
  --white:#fff;
}
*{box-sizing:border-box;margin:0;padding:0}
html,body{width:1200px;height:3766px;overflow:hidden}
body{position:relative;font-family:"Open Sans",Arial,sans-serif;color:var(--text);background:var(--white)}
.abs{position:absolute}
.btn{position:absolute;display:flex;align-items:center;justify-content:center;background:var(--red);color:var(--white);font-weight:700;font-size:13px;text-transform:uppercase;letter-spacing:.3px}
.btn--blue{background:var(--blue)}

/* header */
.site-header{position:absolute;left:0;top:0;width:1200px;height:110px;background:var(--white)}
.logo{position:absolute;left:160px;top:14px;font-size:68px;font-weight:700;color:var(--blue);letter-spacing:-2px;line-height:1}
.nav{position:absolute;left:560px;top:44px;display:flex;gap:18px;font-size:13px;color:#777}
.nav-login{left:845px;top:40px;width:66px;height:32px;font-weight:400}
.nav-demo{left:916px;top:40px;width:126px;height:32px;font-weight:400}

/* hero */
.hero{position:absolute;left:0;top:110px;width:1200px;height:490px;background:radial-gradient(circle at 70% 50%,#1a66b8,var(--blue) 70%)}
.hero-title{position:absolute;left:148px;top:114px;color:var(--white);font-size:45px;font-weight:800;line-height:55px;letter-spacing:.5px}
.hero-btn{left:155px;top:310px;width:126px;height:35px}
.hero-photo{position:absolute;left:620px;top:60px;width:330px;height:430px;border-radius:40px 40px 0 0;background:linear-gradient(160deg,#f2f2f2 0%,#d9c3b0 55%,#b98d72 100%)}

/* intro */
.intro-phone{position:absolute;left:228px;top:662px;width:172px;height:362px;border-radius:26px;background:linear-gradient(#f7f7f7,#dcdcdc);border:2px solid #cfcfcf}
.intro-phone .screen{position:absolute;left:12px;top:52px;width:144px;height:250px;background:linear-gradient(#d98a5a,#7b6a5e 40%,#4d5a64)}
.intro-copy{position:absolute;left:485px;top:700px;width:560px}
.intro-copy h3{font-size:23px;font-weight:700;color:var(--ink);margin-bottom:12px}
.intro-copy p{font-size:13px;line-height:18px;margin-bottom:14px}

/* section titles */
.section-title{position:absolute;left:0;width:1200px;text-align:center;font-size:30px;font-weight:800;color:var(--ink);letter-spacing:.5px}
.section-rule{position:absolute;left:572px;width:56px;height:3px;background:var(--blue-light)}
.section-sub{position:absolute;left:0;width:1200px;text-align:center;font-size:14px;color:var(--muted);font-weight:300}

/* pricing */
.price-card{position:absolute;top:1235px;width:382px;height:505px;background:var(--panel)}
.price-head{height:180px;color:var(--white);text-align:center;padding-top:20px}
.price-head h4{font-size:26px;font-weight:400;line-height:30px}
.price-head .note{font-size:19px;font-weight:300}
.price-amount{display:flex;align-items:baseline;justify-content:flex-start;padding-left:58px;margin-top:14px}
.price-amount .cur{font-size:30px;font-weight:700;margin-right:6px}
.price-amount .num{font-size:54px;font-weight:800;letter-spacing:-1px}
.price-amount .per{font-size:12px;font-weight:700;margin-left:14px}
.price-list{list-style:none;text-align:center;font-size:13px;color:#444;margin-top:20px}
.price-list li{height:36px;line-height:36px}
.price-card .btn{top:455px;height:36px}
.card-yearly .price-head{background:var(--blue)}
.card-monthly .price-head{background:var(--red)}

/* reviews */
.reviews{position:absolute;left:0;top:1810px;width:1200px;height:500px;background:linear-gradient(120deg,var(--blue) 40%,#1f6ec2 100%)}
.reviews .section-title,.reviews .section-sub{color:var(--white)}
.reviews .section-rule{background:var(--white)}
.avatar{position:absolute;left:549px;top:165px;width:102px;height:102px;border-radius:50%;border:4px solid var(--white);background:linear-gradient(#c9b3a6,#8a6c5e)}
.review-box{position:absolute;left:290px;top:228px;width:580px;height:212px;background:#f1f1f1;text-align:center;padding-top:52px}
.stars{display:flex;justify-content:center;gap:2px;margin-bottom:18px}
.stars span{width:15px;height:15px;background:var(--red);display:block}
.review-box p{font-size:13px;line-height:21px;color:#444;padding:0 70px}
.review-box .author{margin-top:18px;font-size:12px}
.arrow-box{position:absolute;top:302px;width:28px;height:42px;background:#f1f1f1;display:flex;align-items:center;justify-content:center}

/* features */
.feature{position:absolute;top:2478px;width:204px;height:250px}
.feature svg.hex{position:absolute;left:0;top:0}
.feature .icon{position:absolute;left:82px;top:40px}
.feature h5{position:absolute;top:106px;left:0;width:204px;text-align:center;font-size:13px;font-weight:700;color:var(--ink)}
.feature p{position:absolute;top:134px;left:32px;width:140px;text-align:center;font-size:10.5px;line-height:14px;color:#777}

/* showcase */
.showcase{position:absolute;left:0;top:2790px;width:1200px;height:675px;background:repeating-linear-gradient(90deg,#fafafa 0 22px,#f2f2f2 22px 44px)}
.demo-phone{position:absolute;top:165px;width:185px;height:400px;border-radius:28px;background:linear-gradient(#fbfbfb,#e2e2e2);border:2px solid #cfcfcf}
.demo-phone .speaker{position:absolute;left:72px;top:30px;width:40px;height:5px;border-radius:3px;background:#c5c5c5}
.demo-phone .screen{position:absolute;left:11px;top:58px;width:159px;height:282px;background:#fff;border:1px solid #ddd}
.demo-phone .bar{height:26px;background:#f4f4f4;border-bottom:2px solid #f07c2a}
.demo-phone .shot{position:absolute;left:4px;right:4px;top:32px;bottom:4px}
.demo-phone .home{position:absolute;left:74px;top:352px;width:34px;height:34px;border-radius:50%;border:2px solid #cfcfcf}
.showcase-btn{left:517px;top:600px;width:192px;height:44px;font-size:16px;font-weight:600}

/* footer */
.site-footer{position:absolute;left:0;top:3465px;width:1200px;height:235px;background:var(--footer)}
.foot-col{position:absolute;top:40px;font-size:12px;color:#666}
.foot-col h6{font-size:17px;font-weight:600;color:var(--red);margin-bottom:12px}
.foot-col ul{list-style:none}
.foot-col li{line-height:23px}
.pay-row{display:flex;gap:10px;margin-bottom:14px}
.pay-row span{width:46px;height:22px;border-radius:3px;background:#d6d6d6;display:block}
.seal-row{display:flex;gap:40px}
.seal{text-align:center;font-size:9px;font-weight:700;color:#3a8a2e;width:70px}
.seal i{display:block;width:46px;height:46px;margin:0 auto 4px;border-radius:50%;background:#b9d7a6}
.newsletter p{line-height:17px;margin-bottom:14px;color:#444}
.newsletter .field{width:222px;height:26px;background:#e0e0e0;font-size:11px;color:#999;padding:5px 10px;margin-bottom:12px}
.newsletter .btn{position:static;width:88px;height:30px;font-size:12px}

.bottom-bar{position:absolute;left:0;top:3700px;width:1200px;height:66px;background:var(--bottom)}
.socials{position:absolute;left:180px;top:20px;display:flex;gap:12px}
.socials span{width:28px;height:28px;background:var(--white);display:block}
.copyright{position:absolute;right:155px;top:27px;font-size:10px;font-weight:700;color:var(--white);letter-spacing:.3px}
</style>
</head>
<body>

<header class="site-header">
  <div class="logo">vorbo</div>
  <nav class="nav"><span>Pricing</span><span>How it Works</span><span>Features</span><span>Partner</span></nav>
  <div class="btn nav-login">Log in</div>
  <div class="btn nav-demo">Request a demo</div>
</header>

<section class="hero">
  <h1 class="hero-title">GET THE FOCUS TO<br>REALIZE YOUR<br>DREAMS</h1>
  <div class="btn hero-btn">Read more</div>
  <div class="hero-photo" role="img" aria-label="Hand holding a smartphone showing a demo shop app"></div>
</section>

<section class="intro">
  <div class="intro-phone"><div class="screen" role="img" aria-label="Demo shop app home screen with product photos"></div></div>
  <div class="intro-copy">
    <h3>Organize your dreams</h3>
    <p>Simply add any dream, enter when you'd like to realize it, and specify the main obstacle. Based on these preferences, Nolio ranks all your dreams and suggests which dream is most vital.</p>
    <h3>Focus on what's essential</h3>
    <p>Activate your most vital dream; choose a category, create milestones, and set weekly action moments. Now, just start chasing your dream with full dedication.</p>
    <h3>Stay motivated</h3>
    <p>The only thing left is to just make it happen. Nolio's dashboard is designed to let you do just that. It shows your progress and tells you what to do next to achieve your upcoming milestone.</p>
  </div>
</section>

<h2 class="section-title" style="top:1098px">OUR PRICING OPTIONS</h2>
<div class="section-rule" style="top:1148px"></div>
<p class="section-sub" style="top:1164px">We take care of your apps for FREE &amp; LIFETIME!</p>

<div class="price-card card-yearly" style="left:180px">
  <div class="price-head">
    <h4>Pay Yearly</h4><div class="note">(Get 2 months for free)</div>
    <div class="price-amount"><span class="cur">€</span><span class="num">165</span><span class="per">/ monthly ex. VAT</span></div>
  </div>
  <ul class="price-list">
    <li>Free Creation and Preview of the App</li><li>No Upfront Costs</li><li>Flexible Terms and Subscription</li>
    <li>App suitable for zelphone &amp; Andrel</li><li>Deep integration with your online store</li><li>Customizable Design</li>
  </ul>
  <div class="btn btn--blue" style="left:16px;width:152px">See all features</div>
  <div class="btn" style="left:218px;width:150px">Build it for me!</div>
</div>

<div class="price-card card-monthly" style="left:625px">
  <div class="price-head">
    <h4>Pay Monthly</h4><div class="note">(Get 2 months for free)</div>
    <div class="price-amount"><span class="cur">€</span><span class="num">199</span><span class="per">/ monthly ex. VAT</span></div>
  </div>
  <ul class="price-list">
    <li>Free Creation and Preview of the App</li><li>No Upfront Costs</li><li>Flexible Terms and Subscription</li>
    <li>App suitable for zelphone &amp; Andrel</li><li>Deep integration with your online store</li><li>Customizable Design</li>
  </ul>
  <div class="btn btn--blue" style="left:16px;width:152px">See all features</div>
  <div class="btn" style="left:218px;width:150px">Build it for me!</div>
</div>

<section class="reviews">
  <h2 class="section-title" style="top:32px;color:#fff">REVIEWS</h2>
  <div class="section-rule" style="top:82px"></div>
  <p class="section-sub" style="top:98px">Read What's The People Are Saying About Us</p>
  <div class="review-box">
    <div class="stars"><span></span><span></span><span></span><span></span><span></span></div>
    <p>Within just 3 weeks 9% of our customers already downloaded the App, which absolutely blew our minds! Hey guys are just awesome, very friendly support, always left you smiling. Special thanks to Joren Keep it up :)</p>
    <div class="author">- Marit, Kids Department</div>
  </div>
  <div class="avatar" role="img" aria-label="Customer portrait"></div>
  <div class="arrow-box" style="left:262px"><svg width="10" height="16" viewBox="0 0 10 16"><path d="M8 1 2 8l6 7" fill="none" stroke="#555" stroke-width="2"/></svg></div>
  <div class="arrow-box" style="left:870px"><svg width="10" height="16" viewBox="0 0 10 16"><path d="M2 1l6 7-6 7" fill="none" stroke="#555" stroke-width="2"/></svg></div>
</section>

<h2 class="section-title" style="top:2362px">FUNCTIONALITIES OVERVIEW</h2>
<div class="section-rule" style="top:2412px"></div>
<p class="section-sub" style="top:2428px">Learn more about this feature packed App</p>

<div class="feature" style="left:178px">
  <svg class="hex" width="204" height="250" viewBox="0 0 204 250"><polygon points="102,3 200,64 200,186 102,247 4,186 4,64" fill="#fff" stroke="#f5a0a3" stroke-width="2"/></svg>
  <svg class="icon" width="40" height="40" viewBox="0 0 40 40"><path d="M20 4v20M12 16l8 8 8-8" stroke="#ee4a50" stroke-width="4" fill="none"/><path d="M4 24v10h32V24" stroke="#ee4a50" stroke-width="4" fill="none"/></svg>
  <h5>Fast &amp; Easy Set-up</h5>
  <p>It only takes half a day to make your App. Import the content of your existing online store, design the App!</p>
</div>
<div class="feature" style="left:385px">
  <svg class="hex" width="204" height="250" viewBox="0 0 204 250"><polygon points="102,3 200,64 200,186 102,247 4,186 4,64" fill="#fff" stroke="#f5a0a3" stroke-width="2"/></svg>
  <svg class="icon" width="40" height="40" viewBox="0 0 40 40"><rect x="4" y="8" width="28" height="28" fill="none" stroke="#ee4a50" stroke-width="3"/><path d="M10 20l7 7L36 6" stroke="#ee4a50" stroke-width="4" fill="none"/></svg>
  <h5>No Obligations</h5>
  <p>It only takes half a day to make your App. Import the content of your existing online store, design the App!</p>
</div>
<div class="feature" style="left:600px">
  <svg class="hex" width="204" height="250" viewBox="0 0 204 250"><polygon points="102,3 200,64 200,186 102,247 4,186 4,64" fill="#fff" stroke="#f5a0a3" stroke-width="2"/></svg>
  <svg class="icon" width="40" height="40" viewBox="0 0 40 40"><rect x="3" y="8" width="34" height="24" fill="#ee4a50"/><path d="M3 8l17 13L37 8" stroke="#fff" stroke-width="2" fill="none"/></svg>
  <h5>Unlimited Push Messages</h5>
  <p>It only takes half a day to make your App. Import the content of your existing online store, design the App!</p>
</div>
<div class="feature" style="left:816px">
  <svg class="hex" width="204" height="250" viewBox="0 0 204 250"><polygon points="102,3 200,64 200,186 102,247 4,186 4,64" fill="#fff" stroke="#f5a0a3" stroke-width="2"/></svg>
  <svg class="icon" width="40" height="40" viewBox="0 0 40 40"><rect x="7" y="3" width="26" height="34" rx="4" fill="#ee4a50"/><rect x="11" y="8" width="18" height="22" fill="#fff"/></svg>
  <h5>Orvos &amp; Andrel</h5>
  <p>It only takes half a day to make your App. Import the content of your existing online store, design the App!</p>
</div>

<section class="showcase">
  <h2 class="section-title" style="top:38px">SHOWCASE</h2>
  <div class="section-rule" style="top:88px"></div>
  <p class="section-sub" style="top:104px">Your effortless business management</p>

  <div class="demo-phone" style="left:182px"><div class="speaker"></div><div class="screen"><div class="bar"></div><div class="shot" role="img" aria-label="Demo shop home screen with category photos" style="background:linear-gradient(#c98a62,#6f675f 50%,#4b5762)"></div></div><div class="home"></div></div>
  <div class="demo-phone" style="left:405px"><div class="speaker"></div><div class="screen"><div class="bar"></div><div class="shot" role="img" aria-label="Demo shop product grid" style="background:linear-gradient(#d9c4a8,#9a7a55 50%,#e6e0d4)"></div></div><div class="home"></div></div>
  <div class="demo-phone" style="left:622px"><div class="speaker"></div><div class="screen"><div class="bar"></div><div class="shot" role="img" aria-label="Demo shop product list with prices" style="background:linear-gradient(#f2f2f2,#d8d2c8 50%,#f0f0f0)"></div></div><div class="home"></div></div>
  <div class="demo-phone" style="left:850px"><div class="speaker"></div><div class="screen"><div class="bar"></div><div class="shot" role="img" aria-label="Demo shop product detail page" style="background:linear-gradient(#ffffff,#e8e4e6 60%,#f07c2a 94%)"></div></div><div class="home"></div></div>

  <div class="btn showcase-btn">Request a demo</div>
</section>

<footer class="site-footer">
  <div class="foot-col" style="left:180px"><h6>Company</h6><ul><li>Company</li><li>Why Vorbo?</li><li>Blog</li><li>Contact us</li></ul></div>
  <div class="foot-col" style="left:350px"><h6>Support</h6><ul><li>Support Desk</li><li>Setup Guide</li><li>Docs &amp; Release Notes</li><li>Customization</li></ul></div>
  <div class="foot-col" style="left:532px"><h6>We Accept</h6>
    <div class="pay-row"><span></span><span></span><span></span></div>
    <div class="seal-row"><div class="seal"><i></i>SECURE</div><div class="seal"><i></i>100% SECURE CHECKOUT PAGE</div></div>
  </div>
  <div class="foot-col newsletter" style="left:800px;width:240px"><h6>Newsletter</h6>
    <p>Get exclusive deals and the latest news direct to your inbox, sign up today!</p>
    <div class="field">Enter your email address</div>
    <div class="btn">Subscribe</div>
  </div>
</footer>

<div class="bottom-bar">
  <div class="socials"><span></span><span></span><span></span><span></span></div>
  <div class="copyright">© VORBO APP 2016 ALL RIGHTS RESERVED</div>
</div>

</body>
</html>
```